Classy, Elegant, Simple Business Card Design

Looking to have a classy, simple, and elegant design. Want a top notch designed business card. I really like the look of the new torvane credit card. I also like the design I attached. I am trying to reach 21-29 year old females for booking us for there wedding or event. We offer Disc Jockey Service, Photo Booth Rentals, and Uplighting .

Target Market(s)

21-28 year old females

Contact Information for Business Card

Has to have logo, website, email, and phone number

Font styles to use
Other font styles liked:
• open to font choice, modern, clean
Designer to choose
33a6d7
0791cd
0555a3
ffffff

Requirements
Must have
• Has to have logo, website, email, and phone number
Nice to have
• I really like the design of the new torvane credit card. I also included my logo and some designs I like
Should not have
• clutter or too much info

```html
<!DOCTYPE html>
<html lang="en">
<head>
<meta charset="utf-8">
<title>Quillaro Event Group – Business Card</title>
<link rel="stylesheet" href="https://fonts.googleapis.com/css2?family=Questrial&family=Open+Sans:wght@400;600;700&display=swap">
<style>
  :root {
    --backdrop: #3a3a3c;
    --card: #1f2023;
    --white: #ffffff;
    --sky: #33a6d7;
    --azure: #0791cd;
    --navy: #0555a3;
    --silver: #9a9ca0;
  }
  * { margin: 0; padding: 0; box-sizing: border-box; }
  html, body { width: 799px; height: 1200px; overflow: hidden; }
  body {
    background: var(--backdrop);
    display: flex;
    flex-direction: column;
    align-items: center;
    justify-content: space-around;
    padding: 70px 0;
    font-family: "Open Sans", sans-serif;
  }
  .card {
    position: relative;
    width: 620px;
    height: 354px;
    background: var(--card);
    border-radius: 4px;
    overflow: hidden;
    box-shadow: 0 18px 40px rgba(0,0,0,0.45);
  }

  .brand-seal {
    position: absolute;
    border-radius: 50%;
    display: flex; align-items: center; justify-content: center;
  }
  .brand-seal__name {
    font-family: "Questrial", sans-serif;
    letter-spacing: 2px;
    color: var(--sky);
    text-transform: uppercase;
    white-space: nowrap;
  }

  /* Front */
  .card--front .brand-seal {
    left: 50%; top: 50%;
    width: 190px; height: 190px;
    transform: translate(-50%, -50%);
    border: 2px solid var(--silver);
  }
  .card--front .brand-seal__name { font-size: 22px; }

  /* Back */
  .card--back .contact {
    position: absolute;
    left: 44px; top: 46px;
  }
  .company {
    font-family: "Questrial", sans-serif;
    font-weight: 400;
    color: var(--white);
    font-size: 27px;
    letter-spacing: 1px;
    line-height: 1;
    text-transform: uppercase;
  }
  .company__sub {
    display: block;
    font-family: "Questrial", sans-serif;
    color: var(--silver);
    font-size: 10px;
    letter-spacing: 4px;
    margin-top: 3px;
    margin-left: 62px;
    text-transform: uppercase;
  }
  .person { margin-top: 14px; }
  .person__name {
    font-weight: 700;
    font-size: 21px;
    color: var(--azure);
    line-height: 1.1;
  }
  .person__role {
    font-size: 14px;
    color: var(--white);
    margin-top: 2px;
  }
  .details { list-style: none; margin-top: 16px; }
  .details__item {
    display: flex; align-items: center; gap: 10px;
    color: var(--white);
    font-size: 14px;
    line-height: 1;
    margin-bottom: 9px;
  }
  .details__icon { width: 13px; height: 13px; flex: none; }

  .card--back .brand-seal {
    left: 385px; top: 62px;
    width: 220px; height: 220px;
    border: 2px solid var(--navy);
  }
  .card--back .brand-seal__name { font-size: 24px; }
</style>
</head>
<body>

  <section class="card card--front" aria-label="Card front">
    <div class="brand-seal">
      <span class="brand-seal__name">Quillaro</span>
    </div>
  </section>

  <section class="card card--back" aria-label="Card back">
    <div class="contact">
      <h1 class="company">Quillaro<span class="company__sub">Event Group</span></h1>
      <div class="person">
        <p class="person__name">Dana Reyes</p>
        <p class="person__role">Founder &amp; CEO</p>
      </div>
      <ul class="details">
        <li class="details__item">
          <svg class="details__icon" viewBox="0 0 16 16" aria-hidden="true"><path fill="#0791cd" d="M3.5 1.5l2.5 0 1 3.5-1.6 1.2a8 8 0 0 0 4.4 4.4L11 9l3.5 1v2.5c0 .8-.7 1.5-1.5 1.5A12 12 0 0 1 2 3c0-.8.7-1.5 1.5-1.5z"/></svg>
          <span>555 0148 0148</span>
        </li>
        <li class="details__item">
          <svg class="details__icon" viewBox="0 0 16 16" aria-hidden="true"><rect x="1" y="3" width="14" height="10" rx="1" fill="#0791cd"/><path d="M1.5 3.5L8 9l6.5-5.5" stroke="#1f2023" stroke-width="1.3" fill="none"/></svg>
          <span>dana@quillaro.com</span>
        </li>
        <li class="details__item">
          <svg class="details__icon" viewBox="0 0 16 16" aria-hidden="true"><circle cx="8" cy="8" r="6.5" fill="none" stroke="#0791cd" stroke-width="1.5"/><ellipse cx="8" cy="8" rx="2.8" ry="6.5" fill="none" stroke="#0791cd" stroke-width="1.2"/><path d="M1.5 8h13" stroke="#0791cd" stroke-width="1.2"/></svg>
          <span>www.quillaro.com</span>
        </li>
      </ul>
    </div>
    <div class="brand-seal">
      <span class="brand-seal__name">Quillaro</span>
    </div>
  </section>

</body>
</html>
```